Phuket Thailand - Rental Villa Website

I have a villa for rent in Thailand and require a website - i need to demo pictures/walk through video, local attractions, villa facilities description plus seaonal rates and online booking.

Industry/Entity Type

Rental

Coding

Coded - Design and coding required

```html
<!DOCTYPE html>
<html lang="en">
<head>
<meta charset="utf-8">
<title>Villa Rental</title>
<link href="https://fonts.googleapis.com/css2?family=Roboto:wght@300;400;500;700&family=Roboto+Condensed:wght@700&display=swap" rel="stylesheet">
<style>
:root{
  --teal:#3aa6c0;
  --black:#050505;
  --page:#efefef;
  --white:#ffffff;
  --ink:#2b2b2b;
  --muted:#555555;
  --rule:#dcdcdc;
  --panel:#474747;
  --footer:#1d1819;
  --field:#e9e9e9;
  --bar:#1b1b1b;
}
*{margin:0;padding:0;box-sizing:border-box}
html,body{width:1200px;height:2542px;overflow:hidden}
body{position:relative;background:var(--page);font-family:'Roboto',sans-serif;color:var(--ink)}
.abs{position:absolute}

/* header */
.site-header{left:0;top:0;width:1200px;height:75px;background:var(--black)}
.brand{left:102px;top:22px;color:var(--white);font-weight:700;font-size:19px;letter-spacing:2px}
.main-nav{top:28px;color:var(--white);font-size:15px}
.main-nav span{position:absolute;white-space:nowrap}

/* hero */
.hero{left:0;top:75px;width:1200px;height:573px;background:linear-gradient(180deg,#1a2f6b 0%,#2a4f8f 30%,#3e5d5a 60%,#2b8a8f 78%,#1f3a3a 100%)}
.hero-arrow{top:318px}
.dots{top:541px;left:554px;display:flex;gap:5px}
.dots i{display:block;width:16px;height:16px;border-radius:50%;border:2px solid var(--white);background:rgba(255,255,255,.6)}
.dots i.on{background:#333}

/* booking */
.booking{left:102px;top:576px;width:995px;height:72px;background:var(--bar);box-shadow:0 10px 18px rgba(0,0,0,.35)}
.field{top:14px;height:44px;background:var(--white);font-size:13px;color:var(--muted);padding:14px 12px;border-radius:2px}
.field .addon{position:absolute;right:0;top:0;width:48px;height:44px;background:var(--field);display:flex;align-items:center;justify-content:center}
.book-btn{top:14px;left:862px;width:116px;height:44px;background:var(--teal);color:var(--white);font-size:14px;font-weight:500;display:flex;align-items:center;justify-content:center}

/* attractions */
.card{background:var(--white);left:100px;width:998px}
.attractions{top:685px;height:320px}
.section-title{font-size:23px;font-weight:400;color:var(--ink)}
.section-title em{font-style:normal;color:var(--teal)}
.attractions .section-title{top:25px;width:100%;text-align:center}
.place{top:92px;width:300px;text-align:center;font-size:13.5px;line-height:22px;color:#444}
.pin-ring{width:84px;height:84px;border-radius:50%;border:1px solid #c9c9c9;margin:0 auto 20px;display:flex;align-items:center;justify-content:center}
.place b{display:block;font-weight:700;color:#222}
.place .tel{color:var(--teal);font-weight:500;margin-top:12px}
.divider{top:93px;width:1px;height:188px;background:var(--rule)}

/* video */
.video{top:1017px;height:363px;background:linear-gradient(100deg,#3a2e28 0%,#5b514a 35%,#7d7a74 60%,#9a9a93 80%,#6a6f68 100%)}
.video-title{left:98px;top:112px;font-family:'Roboto Condensed',sans-serif;font-weight:700;font-size:35px;line-height:40px;color:var(--white)}
.video-btn{left:100px;top:203px;width:205px;height:51px;background:var(--teal);color:var(--white);font-family:'Roboto Condensed',sans-serif;font-weight:700;font-size:19px;display:flex;align-items:center;justify-content:center}
.play{left:458px;top:141px}

/* facilities */
.facilities{top:1392px;height:383px}
.facilities .section-title{left:36px;top:30px}
.facilities p{left:36px;top:78px;width:550px;font-size:13px;line-height:24.7px;color:#333}
.amenity{font-size:14px;color:#222;display:flex;align-items:center;gap:12px}
.amenity i{width:22px;height:22px;background:var(--teal);display:flex;align-items:center;justify-content:center}
.facility-photo{left:642px;top:79px;width:322px;height:270px;border:3px solid #e2e2e2;background:linear-gradient(180deg,#9aa3a8 0%,#7d8a86 40%,#6b5646 60%,#c4bfb6 100%)}

/* rates */
.rates{left:100px;top:1786px;width:998px;height:421px;background:var(--panel)}
.tab{top:21px;height:47px;width:139px;color:var(--white);font-size:16px;display:flex;align-items:center;justify-content:center}
.tab.active{left:20px;background:var(--teal);font-weight:500}
.tab.idle{left:163px;background:#6a6a6a}
.rate-table{left:20px;top:84px;width:960px;border-collapse:collapse;background:var(--white);font-size:13px;color:#333}
.rate-table th{background:var(--teal);color:var(--white);font-weight:500;height:42px;font-size:14px;border:1px solid #6a6a6a}
.rate-table td{border:1px solid #6a6a6a;vertical-align:top;padding:14px 18px;line-height:24.5px}
.rate-note{right:18px;top:380px;color:var(--white);font-size:15px}

/* footer */
.site-footer{left:0;top:2231px;width:1200px;height:311px;background:var(--footer);color:var(--white)}
.footer-brand{left:100px;top:34px;font-weight:700;font-size:19px;letter-spacing:2px;line-height:31px}
.footer-brand span{display:block;padding-left:34px}
.footer-nav{right:103px;top:50px;font-size:13px}
.footer-rule{left:100px;width:997px;height:1px;background:#3a3536}
.footer-label{top:136px;font-size:15px}
.socials{left:104px;top:164px;display:flex;gap:8px}
.socials i{display:block;width:38px;height:38px;border-radius:50%;border:1.5px solid var(--white)}
.input{top:164px;height:46px;background:#3a3a3a;color:#aaa;font-size:13px;padding:15px 16px}
.input-btn{top:164px;height:46px;background:#000;display:flex;align-items:center;justify-content:center;font-size:14px;color:var(--white)}
.copyright{left:103px;top:268px;font-size:11px;color:#bbb}
</style>
</head>
<body>

<header class="site-header abs">
  <div class="brand abs">VILLA RENTAL</div>
  <nav class="main-nav abs">
    <span style="left:446px">Home</span>
    <span style="left:525px">About</span>
    <span style="left:602px">Services</span>
    <span style="left:698px">Facilities</span>
    <span style="left:798px">Locations</span>
    <span style="left:902px">Contact</span>
    <span style="left:981px">1-800.XXX.XXXX</span>
  </nav>
</header>

<section class="hero abs" role="img" aria-label="Luxury villa with pool and terrace at dusk beside the water">
  <svg class="hero-arrow abs" style="left:84px" width="24" height="50" viewBox="0 0 24 50"><path d="M20 4 L4 25 L20 46" fill="none" stroke="#fff" stroke-width="5" opacity=".8"/></svg>
  <svg class="hero-arrow abs" style="left:1060px" width="24" height="50" viewBox="0 0 24 50"><path d="M4 4 L20 25 L4 46" fill="none" stroke="#fff" stroke-width="5" opacity=".5"/></svg>
  <div class="dots abs"><i></i><i class="on"></i><i></i><i></i></div>
</section>

<form class="booking abs">
  <div class="field abs" style="left:15px;width:295px">Name</div>
  <div class="field abs" style="left:323px;width:168px">Chek in
    <span class="addon"><svg width="14" height="14" viewBox="0 0 14 14"><rect x="1" y="2" width="12" height="11" fill="none" stroke="#666" stroke-width="1.4"/><path d="M1 5h12M4 0v3M10 0v3M4 8h2M8 8h2M4 10.5h2M8 10.5h2" stroke="#666" stroke-width="1.4"/></svg></span></div>
  <div class="field abs" style="left:505px;width:169px">Chek out
    <span class="addon"><svg width="14" height="14" viewBox="0 0 14 14"><rect x="1" y="2" width="12" height="11" fill="none" stroke="#666" stroke-width="1.4"/><path d="M1 5h12M4 0v3M10 0v3M4 8h2M8 8h2M4 10.5h2M8 10.5h2" stroke="#666" stroke-width="1.4"/></svg></span></div>
  <div class="field abs" style="left:685px;width:169px">Bedrooms
    <span class="addon"><svg width="10" height="16" viewBox="0 0 10 16"><path d="M1 6 L5 1 L9 6Z M1 10 L5 15 L9 10Z" fill="#666"/></svg></span></div>
  <div class="book-btn abs">BOOK NOW</div>
</form>

<section class="card attractions abs">
  <h2 class="section-title abs">Local <em>Attractions</em></h2>
  <div class="divider abs" style="left:344px"></div>
  <div class="divider abs" style="left:683px"></div>
  <div class="place abs" style="left:13px">
    <div class="pin-ring"><svg width="16" height="24" viewBox="0 0 16 24"><path d="M8 0C3.6 0 0 3.6 0 8c0 6 8 16 8 16s8-10 8-16c0-4.4-3.6-8-8-8z" fill="#555"/><circle cx="8" cy="8" r="3" fill="#fff"/></svg></div>
    <b>Bangkok</b>4th Floor Tower, 18/2 Lotus Lane<br>Bangkok 10330,&nbsp; Thailand
    <div class="tel">Tel: +66-2-555-0142</div>
  </div>
  <div class="place abs" style="left:364px">
    <div class="pin-ring"><svg width="16" height="24" viewBox="0 0 16 24"><path d="M8 0C3.6 0 0 3.6 0 8c0 6 8 16 8 16s8-10 8-16c0-4.4-3.6-8-8-8z" fill="#555"/><circle cx="8" cy="8" r="3" fill="#fff"/></svg></div>
    <b>Phuket</b>120-122 Palm Grove Road<br>Phuket, Thailand
    <div class="tel">Tel: +66-2-555-0142</div>
  </div>
  <div class="place abs" style="left:686px">
    <div class="pin-ring"><svg width="16" height="24" viewBox="0 0 16 24"><path d="M8 0C3.6 0 0 3.6 0 8c0 6 8 16 8 16s8-10 8-16c0-4.4-3.6-8-8-8z" fill="#555"/><circle cx="8" cy="8" r="3" fill="#fff"/></svg></div>
    <b>Bangkok</b>95 Orchid Road,<br>Bangkok, Thailand
    <div class="tel">Tel: +66-2-555-0142</div>
  </div>
</section>

<section class="card video abs" role="img" aria-label="Villa bedroom interior with a view onto the garden">
  <h2 class="video-title abs">VILLA RENTAL<br>SERVICE</h2>
  <div class="video-btn abs">WATCH OUR VIDEO</div>
  <svg class="play abs" width="80" height="80" viewBox="0 0 80 80"><circle cx="40" cy="40" r="35" fill="none" stroke="#fff" stroke-width="7"/><path d="M32 24 L56 40 L32 56Z" fill="#fff"/></svg>
</section>

<section class="card facilities abs">
  <h2 class="section-title abs">Villa <em>Facilities</em></h2>
  <p class="abs">Contrary to popular belief, Lorem Ipsum is not simply random text. It has roots in a piece of classical Latin literature from 45 BC, making it over 2000 years old. Arthur Penhallow, a Latin professor at Westbrook College in Vermont, looked up one of the more obscure Latin words, consectetur, from a Lorem Ipsum passage, and going through the cites of the word in classical literature, discovered the undoubtable source.</p>
  <div class="amenity abs" style="left:37px;top:217px"><i><svg width="8" height="10" viewBox="0 0 8 10"><path d="M1.5 1 L6 5 L1.5 9" fill="none" stroke="#fff" stroke-width="2"/></svg></i>Swimming Pool</div>
  <div class="amenity abs" style="left:242px;top:217px"><i><svg width="8" height="10" viewBox="0 0 8 10"><path d="M1.5 1 L6 5 L1.5 9" fill="none" stroke="#fff" stroke-width="2"/></svg></i>Daily Housekeeping</div>
  <div class="amenity abs" style="left:464px;top:217px"><i><svg width="8" height="10" viewBox="0 0 8 10"><path d="M1.5 1 L6 5 L1.5 9" fill="none" stroke="#fff" stroke-width="2"/></svg></i>Pool Towels</div>
  <div class="amenity abs" style="left:37px;top:258px"><i><svg width="8" height="10" viewBox="0 0 8 10"><path d="M1.5 1 L6 5 L1.5 9" fill="none" stroke="#fff" stroke-width="2"/></svg></i>Sun Loungers at pool</div>
  <div class="amenity abs" style="left:242px;top:258px"><i><svg width="8" height="10" viewBox="0 0 8 10"><path d="M1.5 1 L6 5 L1.5 9" fill="none" stroke="#fff" stroke-width="2"/></svg></i>Turn over service</div>
  <div class="amenity abs" style="left:464px;top:258px"><i><svg width="8" height="10" viewBox="0 0 8 10"><path d="M1.5 1 L6 5 L1.5 9" fill="none" stroke="#fff" stroke-width="2"/></svg></i>Beach Towels</div>
  <div class="amenity abs" style="left:37px;top:302px"><i><svg width="8" height="10" viewBox="0 0 8 10"><path d="M1.5 1 L6 5 L1.5 9" fill="none" stroke="#fff" stroke-width="2"/></svg></i>Safe deposit box</div>
  <div class="facility-photo abs" role="img" aria-label="Covered terrace overlooking green hills and a lake"></div>
</section>

<section class="rates abs">
  <div class="tab active abs">By Season</div>
  <div class="tab idle abs">By Date</div>
  <table class="rate-table abs">
    <thead><tr>
      <th style="width:168px">Season</th><th style="width:239px">Period</th><th style="width:181px">Price (per night)</th><th style="width:202px">14 nights or more</th><th>Minimum stay</th>
    </tr></thead>
    <tbody>
      <tr style="height:100px"><td>Low Season</td><td>09 Jan 2015 to 02 Apr 2015<br>11 Apr 2015 to 15 Jun 2015<br>01 Sep 2015 to 18 Dec 2015</td><td>US$ 1095 ++</td><td>US$ 931 ++</td><td>2 Nights</td></tr>
      <tr style="height:86px"><td>High Season</td><td>03 Apr 2015 to 10 Apr 2015<br>16 Jun 2015 to 31 Aug 2015</td><td>US$ 1290 ++</td><td>US$ 1161 ++</td><td>5 Nights</td></tr>
      <tr style="height:60px"><td>Peak Season</td><td>19 Dec 2015 to 08 Jan 2016</td><td>US$ 1470 ++</td><td>US$ 1397 ++</td><td>7 Nights</td></tr>
    </tbody>
  </table>
  <div class="rate-note abs">Last minute bookings, checking in before 2015-Feb-15, enjoy a 10% discount.</div>
</section>

<footer class="site-footer abs">
  <div class="footer-brand abs">VILLA RENTAL<span>SERVICE</span></div>
  <nav class="footer-nav abs">Home &nbsp;|&nbsp; About &nbsp;|&nbsp; Services &nbsp;|&nbsp; Facilities &nbsp;|&nbsp; Locations &nbsp;|&nbsp; Contact</nav>
  <div class="footer-rule abs" style="top:114px"></div>
  <div class="footer-label abs" style="left:103px">Follow Us</div>
  <div class="footer-label abs" style="left:385px">Newsletter Subscribe</div>
  <div class="footer-label abs" style="left:853px">Search</div>
  <div class="socials abs"><i></i><i></i><i></i><i></i></div>
  <div class="input abs" style="left:385px;width:230px">Enter email address...</div>
  <div class="input-btn abs" style="left:615px;width:94px">SIGN UP</div>
  <div class="input abs" style="left:856px;width:197px">Enter keyword</div>
  <div class="input-btn abs" style="left:1053px;width:44px"><svg width="16" height="16" viewBox="0 0 16 16"><circle cx="6.5" cy="6.5" r="5" fill="none" stroke="#fff" stroke-width="2"/><path d="M10 10 L15 15" stroke="#fff" stroke-width="2.4"/></svg></div>
  <div class="footer-rule abs" style="top:247px"></div>
  <div class="copyright abs">Copyrights @ 2015 All Rights Reserved</div>
</footer>

</body>
</html>
```